Duct Manufacturing Company new to the industry needs business card and stationary design

we are sheet metal duct manufacturers looking for a business card design to fit my new business logo.
nothing to crazy that will date, but want it to stand out from the crowed.
I'm sure you guys will work it out.

Contact Information for Business Card

Glen Marsh
Director

Address
17 Dorwell St
Karrinvale NSW 2714

0438 760 514

Sales@flowbend.com.au

Font styles to use
Other font styles liked:
• BankGothic md bt

Requirements
Nice to have
• Like the idea of corner rounded to match logo
• like to keep colours flowing
• font I like sharp square not rounded

```html
<!DOCTYPE html>
<html lang="en">
<head>
<meta charset="utf-8">
<title>Flowbend Industries – Business Card</title>
<link href="https://fonts.googleapis.com/css2?family=Michroma&family=Montserrat:wght@400;500&display=swap" rel="stylesheet">
<style>
  :root {
    --bg: #d9d9d9;
    --card-black: #0b0b0c;
    --card-white: #ffffff;
    --blue-light: #1386cf;
    --blue-dark: #0d3f8f;
    --green: #7cc242;
    --brand: #7cc242;
    --text-light: #ffffff;
  }
  * { margin: 0; padding: 0; box-sizing: border-box; }
  html, body { width: 1200px; height: 1200px; overflow: hidden; }
  body {
    background: var(--bg);
    position: relative;
    font-family: "Montserrat", Arial, sans-serif;
  }
  .card {
    position: absolute;
    left: 250px;
    width: 700px;
    height: 400px;
    border-radius: 28px;
    overflow: hidden;
    box-shadow: 0 6px 18px rgba(0,0,0,0.18);
  }
  .card--front { top: 150px; background: var(--card-black); }
  .card--back { top: 650px; background: var(--card-white); }

  .brand {
    position: absolute;
    font-family: "Michroma", "Arial Black", sans-serif;
    color: var(--brand);
    line-height: 1.15;
    text-align: center;
    letter-spacing: 2px;
  }
  .card--front .brand {
    left: 0; right: 0; top: 155px;
    font-size: 38px;
  }
  .brand__sub { display: block; font-size: 0.62em; letter-spacing: 6px; }
  .card--back .brand {
    left: 20px; width: 300px; top: 160px;
    font-size: 30px;
  }

  .card__bg { position: absolute; inset: 0; }

  .contact {
    position: absolute;
    left: 420px; top: 90px;
    color: var(--text-light);
  }
  .contact__name {
    font-family: "Michroma", "Arial Black", sans-serif;
    font-size: 21px;
    letter-spacing: 2px;
  }
  .contact__title { font-size: 14px; margin-top: 6px; margin-bottom: 18px; }
  .contact__list { list-style: none; font-size: 16px; line-height: 1.55; }
  .contact__list li { display: flex; align-items: center; gap: 12px; white-space: nowrap; }
  .contact__list svg { width: 15px; height: 15px; flex: none; }
  .contact__list .no-icon { padding-left: 27px; }
</style>
</head>
<body>

  <section class="card card--front">
    <div class="brand">FLOWBEND<span class="brand__sub">INDUSTRIES</span></div>
  </section>

  <section class="card card--back">
    <svg class="card__bg" viewBox="0 0 700 400" preserveAspectRatio="none">
      <defs>
        <linearGradient id="blueFlow" x1="0" y1="0" x2="0.3" y2="1">
          <stop offset="0" stop-color="var(--blue-light)"/>
          <stop offset="1" stop-color="var(--blue-dark)"/>
        </linearGradient>
      </defs>
      <path d="M232 0 C330 80 392 220 410 400 L700 400 L700 0 Z" fill="url(#blueFlow)"/>
      <path d="M212 0 C310 80 372 220 392 400" fill="none" stroke="var(--green)" stroke-width="6"/>
    </svg>

    <div class="brand">FLOWBEND<span class="brand__sub">INDUSTRIES</span></div>

    <div class="contact">
      <div class="contact__name">GLEN MARSH</div>
      <div class="contact__title">Director</div>
      <ul class="contact__list">
        <li>
          <svg viewBox="0 0 16 16" aria-hidden="true"><path fill="#fff" d="M3 2h3l1 3-2 1a8 8 0 0 0 5 5l1-2 3 1v3c0 1-1 1-1 1C7 14 2 9 2 3c0 0 0-1 1-1z"/></svg>
          0438 760 514
        </li>
        <li>
          <svg viewBox="0 0 16 16" aria-hidden="true"><g fill="none" stroke="#fff" stroke-width="1.4"><circle cx="8" cy="8" r="6.3"/><ellipse cx="8" cy="8" rx="2.8" ry="6.3"/><path d="M1.7 8h12.6"/></g></svg>
          flowbend.com.au
        </li>
        <li>
          <svg viewBox="0 0 16 16" aria-hidden="true"><rect x="1.5" y="3.5" width="13" height="9" fill="#fff"/><path d="M1.5 3.5l6.5 5 6.5-5" fill="none" stroke="#0d3f8f" stroke-width="1.2"/></svg>
          Sales@flowbend.com.au
        </li>
        <li class="no-icon">17 Dorwell St</li>
        <li class="no-icon">Karrinvale NSW 2714</li>
      </ul>
    </div>
  </section>

</body>
</html>
```